Kelvaro.ch is looking for business card letterhead and envelope C5 with WOW effect

We need a strong business card for our company Kelvaro.ch, logo is available. You want a black or dark background on which the logo Stark r% 26 # 252; appears. Letterhead and envelope in C5 format should be in a similar design, but does not have to be We need a strong business card for our company Kelvaro.ch, logo is available. A black or dark background is desired, on which the logo Stark comes across. The letterhead and the envelope in C5 format should have a similar design.

Target Market(s)

Private customers as well as entrepreneurs

Contact Information for Business Card

E-mail: info@kelvaro-example.ch
Web.www.Kelvaro-example.ch
Tel: +41 ( 0 ) 79 482 6037
Adresse:
Lindenweg 14
9406 Tarnbach

Hier kann man Icons verwenden für Email,Tel und Adressse

Font styles to use
Other font styles liked:
• Dubai,bold

Colors

Designer to choose colors to be used in the design.

Requirements
Must have
• WOW effect
Nice to have
• R% 26 # 252; back business card with our service listings. - VEHICLE LABELING - SHOP WINDOW LABELING - STICKERS AND MUCH MORE ... in red color

```html
<!DOCTYPE html>
<html lang="en">
<head>
<meta charset="utf-8">
<title>Kelvaro.ch – Business Card</title>
<link href="https://fonts.googleapis.com/css2?family=Russo+One&family=Ubuntu:wght@400;700&display=swap" rel="stylesheet">
<style>
  :root {
    --stage: #1c1c1c;
    --card: #0b0b0b;
    --yellow: #fdc91c;
    --yellow-deep: #d9a912;
    --white: #f4f4f4;
    --muted: #e6e6e6;
  }
  * { box-sizing: border-box; margin: 0; padding: 0; }
  html, body { width: 1200px; height: 900px; overflow: hidden; }
  body {
    background: radial-gradient(circle at 60% 30%, #333 0%, var(--stage) 70%);
    font-family: "Ubuntu", sans-serif;
    position: relative;
  }
  .card {
    position: absolute;
    left: 250px;
    width: 700px;
    height: 380px;
    background: var(--card);
    overflow: hidden;
    box-shadow: 0 14px 30px rgba(0,0,0,.6);
  }
  .card::after {
    content: "";
    position: absolute;
    right: 0; top: 0; bottom: 0;
    width: 4px;
    background: var(--yellow);
  }
  .card-front { top: 50px; }
  .card-back { top: 470px; }

  .front-art {
    position: absolute;
    left: 20px; top: 10px;
    width: 320px; height: 360px;
    background: radial-gradient(closest-side, var(--yellow) 0%, var(--yellow-deep) 50%, rgba(11,11,11,0) 100%);
  }
  .front-texture {
    position: absolute;
    right: 10px; top: 40px;
    width: 340px; height: 330px;
    background: radial-gradient(closest-side, #1d1d1d 0%, rgba(11,11,11,0) 100%);
  }
  .front-wordmark {
    position: absolute;
    left: 350px; top: 152px;
    display: flex; align-items: center; gap: 14px;
  }
  .brand-square {
    width: 24px; height: 24px;
    background: var(--yellow);
    flex: none;
  }
  .brand-name {
    font-family: "Ubuntu", sans-serif;
    font-weight: 700;
    color: var(--white);
    font-size: 52px;
    line-height: 1;
    letter-spacing: 1px;
    white-space: nowrap;
  }

  .holder { position: absolute; left: 60px; top: 52px; }
  .holder-name {
    font-family: "Russo One", sans-serif;
    color: var(--yellow);
    font-size: 27px;
    letter-spacing: 2px;
    line-height: 1;
  }
  .holder-role { color: var(--muted); font-size: 17px; margin-top: 4px; }

  .contacts { position: absolute; left: 60px; top: 142px; list-style: none; }
  .contacts li {
    display: flex; align-items: center; gap: 12px;
    color: var(--white); font-size: 18px; height: 27px;
    white-space: nowrap;
  }
  .contacts svg { width: 18px; height: 18px; flex: none; }
  .contacts b { color: var(--yellow); font-weight: 700; }

  .divider {
    position: absolute; left: 60px; top: 250px;
    width: 320px; height: 2px; background: var(--yellow);
  }
  .address {
    position: absolute; left: 60px; top: 270px;
    display: flex; align-items: center; gap: 12px;
    color: var(--white); font-size: 18px;
    white-space: nowrap;
  }
  .address svg { width: 20px; height: 20px; }

  .back-wordmark {
    position: absolute; left: 420px; top: 170px;
    display: flex; align-items: center; gap: 12px;
  }
  .back-wordmark .brand-square { width: 18px; height: 18px; }
  .back-wordmark .brand-name { font-size: 34px; }

  .bottom-band { position: absolute; left: 0; bottom: 0; width: 700px; height: 40px; }
</style>
</head>
<body>

<section class="card card-front">
  <div class="front-art" role="img" aria-label="Yellow honeycomb graphic"></div>
  <div class="front-texture" role="img" aria-label="Faint dark honeycomb texture"></div>
  <div class="front-wordmark">
    <span class="brand-square"></span>
    <span class="brand-name">Kelvaro.ch</span>
  </div>
</section>

<section class="card card-back">
  <div class="holder">
    <p class="holder-name">MARLON VEIT</p>
    <p class="holder-role">Owner/ CEO</p>
  </div>

  <ul class="contacts">
    <li>
      <svg viewBox="0 0 24 24" fill="none" stroke="#fdc91c" stroke-width="2" stroke-linejoin="round"><path d="M5 3h4l2 5-2.5 1.5a11 11 0 0 0 6 6L16 13l5 2v4a2 2 0 0 1-2 2A17 17 0 0 1 3 5a2 2 0 0 1 2-2z"/></svg>
      +41 ( 0 ) 79 482 6037
    </li>
    <li>
      <svg viewBox="0 0 24 24" fill="none" stroke="#fdc91c" stroke-width="2" stroke-linejoin="round"><rect x="2" y="5" width="20" height="14"/><path d="M2 5l10 8 10-8"/></svg>
      info@kelvaro-example.ch
    </li>
    <li>
      <svg viewBox="0 0 24 24" fill="none" stroke="#fdc91c" stroke-width="2"><circle cx="12" cy="12" r="10"/><path d="M2 12h20M12 2c3 3 3 17 0 20M12 2c-3 3-3 17 0 20"/></svg>
      <span>www.<b>Kelvaro</b>-example.ch</span>
    </li>
  </ul>

  <div class="divider"></div>

  <div class="address">
    <svg viewBox="0 0 24 24" fill="none" stroke="#fdc91c" stroke-width="2" stroke-linejoin="round"><path d="M3 11l9-8 9 8v10H3z"/><path d="M10 21v-6h4v6"/></svg>
    Lindenweg 14, 9406 Tarnbach
  </div>

  <div class="back-wordmark">
    <span class="brand-square"></span>
    <span class="brand-name">Kelvaro.ch</span>
  </div>

  <svg class="bottom-band" viewBox="0 0 700 40" preserveAspectRatio="none">
    <polygon points="0,28 440,28 428,40 0,40" fill="#fdc91c"/>
    <polygon points="462,14 680,14 658,40 440,40" fill="#fdc91c"/>
  </svg>
</section>

</body>
</html>
```